Business Card Design

We like to use greens as you will see in our logo (but not TOO much green). We are a Dental Clinic in a somewhat eccentric community. We do not like the dated sharp designs which we see many dentists use. We're looking for something bright and fresh while still maintaining the integrity of the profession. Elegance is not necessarily what we are going for... we need for the design to be "mature" but also up-lifting.

See our logo.
Updates

Project Deadline Extended
Reason: We have 5 designs which we like. But we'd like to see a few more before committing to a design.

Project Deadline Extended
Reason: We are awaiting revisions to this project. We are still welcoming designs while we wait to see if designers are able to provide to us the revisions we require in order to proceed with a selection.

Target Market(s)

Younger families - ages late 20's to early 40's

Industry/Entity Type

Business

Contact Information for Business Card

Corwel T. Banfry DDS 2730 W. Halvert Rd. Ste. 7 Royal Oak, MI 48391 (248)555-0174 FX (248)555-0189 info@BrightwellDentalCareMi.com BrigthwellDentalCareMi.com on the back of the card we need an appointment reminder (For____ Date___ Time____) with "If you are unable to keep your appointment, kindly give 48 hours notice" at the bottom. No use of teeth in the design. DOUBLE SIDED DESIGN

Requirements
Should not have
• The use of pictures of teeth

```html
<!DOCTYPE html>
<html lang="en">
<head>
<meta charset="utf-8">
<title>Brightwell Dental Care – Business Card</title>
<link href="https://fonts.googleapis.com/css2?family=Source+Sans+3:ital,wght@0,400;0,600;0,700;1,400&family=Marcellus+SC&display=swap" rel="stylesheet">
<style>
  :root {
    --green-dark: #1d6a32;
    --green-leaf: #6cbf3f;
    --ink: #333333;
    --ink-soft: #4a4a4a;
    --card: #ffffff;
    --backdrop: #e8e5e0;
    --rule: #555555;
  }
  * { box-sizing: border-box; margin: 0; padding: 0; }
  html, body {
    width: 1200px; height: 1188px; overflow: hidden;
    background: var(--backdrop);
    font-family: "Source Sans 3", "Myriad Pro", sans-serif;
    color: var(--ink);
  }
  .canvas { position: relative; width: 1200px; height: 1188px; }
  .card {
    position: absolute; background: var(--card);
    border: 1px solid #cfcac2;
  }
  .card--front { left: 259px; top: 34px; width: 913px; height: 520px; }
  .card--back  { left: 39px;  top: 611px; width: 916px; height: 520px; overflow: hidden; }

  /* brand name */
  .brand {
    position: absolute; display: flex; align-items: center; gap: 18px;
    color: var(--green-dark); font-weight: 600; line-height: 1.05;
  }
  .brand__dot { flex: none; border-radius: 50%; background: var(--green-leaf); }
  .card--front .brand { left: 43px; top: 80px; font-size: 52px; }
  .card--front .brand__dot { width: 40px; height: 40px; }
  .card--back .brand { left: 74px; top: 30px; font-size: 32px; gap: 12px; }
  .card--back .brand__dot { width: 24px; height: 24px; }

  /* front */
  .doctor { position: absolute; left: 43px; top: 296px; }
  .doctor__name { font-size: 38px; font-weight: 700; color: var(--green-dark); line-height: 1; }
  .doctor__title { font-size: 28px; color: var(--ink); margin-top: 10px; line-height: 1; }
  .contact {
    position: absolute; right: 40px; top: 302px; list-style: none;
    text-align: right; font-size: 24px; line-height: 38px;
  }
  .contact li { display: flex; justify-content: flex-end; align-items: center; gap: 6px; }
  .contact svg { width: 20px; height: 20px; fill: var(--green-dark); }
  .address { position: absolute; right: 40px; top: 472px; font-size: 24px; }

  /* back */
  .appt-title {
    position: absolute; left: 74px; top: 168px;
    font-family: "Marcellus SC", serif; font-size: 38px; color: var(--green-dark);
    letter-spacing: 0.5px;
  }
  .field { position: absolute; font-size: 25px; color: var(--ink-soft); line-height: 1; }
  .dots { position: absolute; border-bottom: 2px dotted var(--rule); height: 0; }
  .slot {
    position: absolute; border: 2px solid #555; border-radius: 5px; height: 36px;
  }
  .days { position: absolute; left: 700px; top: 0; width: 200px; }
  .day { position: absolute; right: 10px; display: flex; align-items: center; gap: 14px; }
  .day span { font-size: 26px; font-weight: 600; color: #222; }
  .day i { display: block; width: 57px; height: 34px; border: 2px solid #555; border-radius: 4px; }
  .notice {
    position: absolute; left: 74px; top: 448px;
    font-size: 26px; font-style: italic; color: #222;
  }
  .band { position: absolute; left: 0; bottom: 0; width: 100%; height: 13px; background: var(--green-dark); }
</style>
</head>
<body>
<main class="canvas">

  <section class="card card--front" aria-label="Business card front">
    <div class="brand"><span class="brand__dot"></span><span>Brightwell<br>Dental Care</span></div>

    <div class="doctor">
      <p class="doctor__name">Corwel T. Banfry</p>
      <p class="doctor__title">DDS</p>
    </div>

    <ul class="contact">
      <li><svg viewBox="0 0 20 20"><path d="M5 2l3 4-2 2c1 2 3 4 6 6l2-2 4 3-2 3C9 18 2 11 2 4z"/></svg>(248)555-0174</li>
      <li><svg viewBox="0 0 20 20"><path d="M5 2h10v5H5zM2 8h16v7h-3v3H5v-3H2zm5 5v3h6v-3z"/></svg>(248)555-0189</li>
      <li><svg viewBox="0 0 20 20"><path d="M2 5h16v11H2zm1 1l7 6 7-6z" fill-rule="evenodd"/></svg>info@BrightwellDentalCareMi.com</li>
      <li><svg viewBox="0 0 20 20"><path d="M10 2a8 8 0 100 16 8 8 0 000-16zm0 1.5c1 1.3 1.8 3 2 5.5H8c.2-2.5 1-4.2 2-5.5zM4 9h2.5c.1-2 .6-3.6 1.3-4.8A6.5 6.5 0 004 9zm9.5 0H16a6.5 6.5 0 00-3.8-4.8c.7 1.2 1.2 2.8 1.3 4.8zM4 11a6.5 6.5 0 003.8 4.8c-.7-1.2-1.2-2.8-1.3-4.8zm4 0c.2 2.5 1 4.2 2 5.5 1-1.3 1.8-3 2-5.5zm5.5 0c-.1 2-.6 3.6-1.3 4.8A6.5 6.5 0 0016 11z"/></svg>BrigthwellDentalCareMi.com</li>
    </ul>

    <p class="address">2730 W. Halvert Rd. Ste. 7 Royal Oak, MI 48391</p>
  </section>

  <section class="card card--back" aria-label="Appointment reminder card back">
    <div class="brand"><span class="brand__dot"></span><span>Brightwell<br>Dental Care</span></div>

    <h2 class="appt-title">YOUR APPOINTMENT</h2>

    <p class="field" style="left:74px; top:246px;">Name :</p>
    <div class="dots" style="left:183px; top:267px; width:506px;"></div>

    <p class="field" style="left:74px; top:311px;">Date :</p>
    <div class="dots" style="left:183px; top:332px; width:167px;"></div>
    <p class="field" style="left:358px; top:311px;">Time :</p>
    <div class="dots" style="left:438px; top:332px; width:155px;"></div>
    <p class="field" style="left:596px; top:311px;">am / pm</p>

    <p class="field" style="left:74px; top:377px;">Next Appointment</p>
    <div class="slot" style="left:327px; top:373px; width:164px;"></div>
    <div class="slot" style="left:530px; top:373px; width:164px;"></div>

    <div class="days">
      <div class="day" style="top:76px;"><span>MON</span><i></i></div>
      <div class="day" style="top:138px;"><span>TUE</span><i></i></div>
      <div class="day" style="top:201px;"><span>WED</span><i></i></div>
      <div class="day" style="top:266px;"><span>THU</span><i></i></div>
      <div class="day" style="top:323px;"><span>FRI</span><i></i></div>
      <div class="day" style="top:379px;"><span>SAT</span><i></i></div>
    </div>

    <p class="notice">If you are unable to keep your appointment, kindly give 48 hours notice</p>
    <div class="band"></div>
  </section>

</main>
</body>
</html>
```